I would like a business card to match my truck wrap and logo. I would like the font to match my existing business card please.

Industry/Entity Type

Painter

Contact Information for Business Card

Rodrigo Fenwar 801-437-2190 Fenwarcoatings.utah@brelmox.com
SERVICES - Custom Paint & Stain, Interior & Exterior, Epoxy Coatings / Garage Floors, Cabinet Refinishing, Log Staining and Refinishing.

Requirements
Nice to have
• I would like to have the white and grey line like the bottom of my vehicle wrap, Light Grey to match my truck also.

```html
<!DOCTYPE html>
<html lang="en">
<head>
<meta charset="UTF-8">
<title>Fenwar Coatings – Business Card</title>
<link rel="stylesheet" href="https://fonts.googleapis.com/css2?family=Arimo:wght@400;700&family=Russo+One&display=swap">
<style>
  :root {
    --page-bg: #e9ebee;
    --brand-blue: #0aa2e2;
    --brand-blue-deep: #1160a6;
    --brand-blue-light: #02aeef;
    --ink-dark: #222629;
    --swoosh-grey: #9a9ca1;
    --card-white: #ffffff;
  }
  * { margin: 0; padding: 0; box-sizing: border-box; }
  html, body {
    width: 1200px; height: 900px; overflow: hidden;
    background: var(--page-bg);
  }
  .canvas {
    position: relative; width: 1200px; height: 900px;
    display: flex; flex-direction: column; align-items: center; justify-content: center; gap: 40px;
  }
  .card {
    position: relative; width: 700px; height: 400px; overflow: hidden;
    box-shadow: 0 6px 18px rgba(0,0,0,0.18);
  }

  /* Back side: services */
  .card-back {
    background: linear-gradient(180deg, var(--brand-blue-light) 0%, var(--brand-blue) 40%, var(--brand-blue-deep) 100%);
  }
  .service-list {
    position: absolute; left: 190px; top: 105px;
    list-style: none;
    font-family: "Arimo", Arial, sans-serif;
    font-size: 24px; line-height: 40px; letter-spacing: 0.5px;
    color: var(--card-white); text-transform: uppercase;
  }
  .service-list li { display: flex; align-items: center; gap: 12px; }
  .service-list li::before {
    content: ""; width: 14px; height: 14px; border-radius: 50%;
    background: var(--card-white); flex: none;
  }

  /* Front side: contact */
  .card-front { background: var(--card-white); }
  .swoosh { position: absolute; inset: 0; width: 700px; height: 400px; }
  .holder-name {
    position: absolute; left: 70px; top: 92px;
    font-family: "Russo One", "Arial Black", sans-serif;
    font-size: 30px; line-height: 36px; letter-spacing: 1px;
    color: var(--brand-blue-deep); text-transform: uppercase;
  }
  .brand-mark {
    position: absolute; right: 50px; top: 148px;
    display: flex; align-items: center; gap: 14px;
  }
  .brand-mark .brand-square {
    width: 30px; height: 30px; background: var(--brand-blue);
  }
  .brand-mark .brand-name {
    font-family: "Russo One", "Arial Black", sans-serif;
    font-size: 34px; line-height: 1; color: var(--brand-blue);
    text-transform: uppercase;
  }
  .contact-list {
    position: absolute; left: 90px; top: 208px;
    list-style: none;
    font-family: "Arimo", Arial, sans-serif;
    font-size: 21px; line-height: 32px; color: var(--ink-dark);
  }
  .contact-list li { display: flex; align-items: center; gap: 12px; }
  .contact-list svg { width: 22px; height: 22px; flex: none; }
</style>
</head>
<body>
<main class="canvas">

  <section class="card card-back" aria-label="Card back: services">
    <ul class="service-list">
      <li>Custom Paint &amp; Stain</li>
      <li>Interior &amp; Exterior</li>
      <li>Epoxy Coatings / Garage Floors</li>
      <li>Cabinet Refinishing</li>
      <li>Log Staining and Refinishing.</li>
    </ul>
  </section>

  <section class="card card-front" aria-label="Card front: contact">
    <svg class="swoosh" viewBox="0 0 700 400" aria-hidden="true">
      <path d="M0,334 C220,336 390,320 500,252 C398,322 220,352 0,354 Z" fill="var(--swoosh-grey)"/>
      <path d="M0,362 C220,362 400,344 540,256 C604,216 652,196 700,188 L700,400 L0,400 Z" fill="var(--brand-blue)"/>
    </svg>

    <h1 class="holder-name">Rodrigo Fenwar</h1>

    <div class="brand-mark">
      <span class="brand-square"></span>
      <span class="brand-name">Fenwar Coatings</span>
    </div>

    <ul class="contact-list">
      <li>
        <svg viewBox="0 0 24 24"><path fill="var(--brand-blue-deep)" d="M6.6 10.8a15.1 15.1 0 0 0 6.6 6.6l2.2-2.2c.3-.3.7-.4 1-.2 1.1.4 2.300.6 3.6.6.6 0 1 .4 1 1V20c0 .6-.4 1-1 1A17 17 0 0 1 3 4c0-.6.4-1 1-1h3.5c.6 0 1 .4 1 1 0 1.3.2 2.5.6 3.6.1.3 0 .7-.2 1z"/></svg>
        801-437-2190
      </li>
      <li>
        <svg viewBox="0 0 24 24"><path fill="var(--brand-blue-deep)" d="M2 5h20v14H2z"/><path d="M2 5l10 8 10-8" fill="none" stroke="#fff" stroke-width="1.6"/></svg>
        Fenwarcoatings.utah@brelmox.com
      </li>
    </ul>
  </section>

</main>
</body>
</html>
```